Tellmora Corporate Stationery

Look for design of all new corporate stationery for an existing insurance broking business that is going through a redesign and move from older partners to younger family members. New Logo is attached. Company is Brisbane based.
Colours in the Logo is Hex #43bed8 and website features a lot of hex #17b8d8. Website front page "A plan to protect you" - headline. "Professional and Individual advice to protect your greatest assets" - tagline.

Stationery required: Business Cards, Letter head, Thank-you cards, Birthday cards, Presentation folders, With Compliment slips and a powerpoint template. We also would like to send a card to all customers with the something along of the lines of "something new".

Target Market(s)

Customers of Insurance business looking at superannuation, life and income protection insurance, investment advice and wills

Industry/Entity Type

Insurance Broker

Font styles to use
Other font styles liked:
• same as logo

Requirements
Must have
• The above designs for new stationery for the new business including:
• Business Cards, Letter head, Thank-you cards, Birthday cards, Presentation folders, With Compliment slips and a powerpoint template. We also would like to send a card to all customers with the something along of the lines of "something new".
Nice to have
• It is a new look - long time family business being passed to next generation - big focus on advice for YOU, individual advice etc..

```html
<!DOCTYPE html>
<html lang="en">
<head>
<meta charset="utf-8">
<title>Tellmora Letterhead</title>
<link href="https://fonts.googleapis.com/css2?family=Maven+Pro:wght@400;500;700&display=swap" rel="stylesheet">
<style>
  :root {
    --brand: #43bed8;
    --brand-deep: #17b8d8;
    --ink: #6f6f6f;
    --ink-dark: #555555;
    --line-grey: #7a7a7a;
    --paper: #ffffff;
    --backdrop: #ffffff;
  }
  * { box-sizing: border-box; margin: 0; padding: 0; }
  html, body { width: 1200px; height: 1000px; overflow: hidden; background: var(--backdrop); }
  body { position: relative; font-family: "Maven Pro", sans-serif; color: var(--ink); }

  .letterhead {
    position: absolute; left: 247px; top: 0; width: 706px; height: 1000px;
    background: var(--paper);
    box-shadow: 2px 0 8px rgba(0,0,0,0.12), -2px 0 8px rgba(0,0,0,0.08);
  }
  .frame { position: absolute; left: 0; top: 0; width: 706px; height: 1000px; }

  .brand {
    position: absolute; left: 42px; top: 44px;
    display: flex; align-items: center; gap: 14px;
  }
  .brand-dot { width: 46px; height: 46px; border-radius: 50%; background: var(--line-grey); }
  .brand-name {
    font-weight: 500; font-size: 30px; letter-spacing: 1px; color: var(--brand);
    line-height: 1;
  }

  .contact-list { position: absolute; left: 502px; top: 41px; width: 164px; list-style: none; }
  .contact-item {
    position: relative; height: 14px; margin-bottom: 3.5px;
    border: 1.3px solid var(--line-grey); border-radius: 7px;
    font-size: 7.5px; color: var(--ink-dark); line-height: 11.5px;
    text-align: right; padding-right: 26px;
  }
  .contact-icon {
    position: absolute; right: -1px; top: -2px; width: 16px; height: 16px;
    background: var(--paper); border: 1.3px solid var(--line-grey); border-radius: 50%;
  }
  .contact-icon svg { position: absolute; left: 2px; top: 2px; width: 10px; height: 10px; }

  .letter-body { position: absolute; left: 104px; top: 143px; width: 498px; }
  .headline { font-weight: 700; font-size: 32px; color: var(--brand); line-height: 40px; margin-bottom: 12px; letter-spacing: 0.3px; }
  .letter-body p { font-size: 10.4px; line-height: 19px; text-align: justify; color: var(--ink); }
  .letter-body p.gap { margin-top: 19px; }

  .sign-off { position: absolute; right: 51px; top: 885px; text-align: right; }
  .signature { font-size: 17px; color: var(--ink-dark); font-weight: 700; }
  .signature-mark { font-style: italic; font-weight: 400; color: #000; margin-right: 4px; }
  .role { margin-top: 12px; font-size: 16px; font-weight: 500; color: var(--brand); letter-spacing: 0.3px; }
</style>
</head>
<body>
<main class="letterhead">
  <svg class="frame" viewBox="0 0 706 1000" aria-hidden="true">
    <rect x="0" y="167" width="20" height="833" fill="var(--brand)"/>
    <g fill="none" stroke="var(--brand-deep)" stroke-width="2">
      <polyline points="288,107 19,107 19,925 330,925"/>
      <polyline points="23,110 23,920 330,920"/>
      <polyline points="28,110 28,903 290,903"/>
      <polyline points="33,110 33,885"/>
      <line x1="188" y1="909" x2="330" y2="909"/>
      <line x1="108" y1="915" x2="330" y2="915"/>
      <line x1="330" y1="914" x2="358" y2="914"/>
      <path d="M666,871 H403 A43,43 0 0 0 403,957 H666"/>
    </g>
  </svg>

  <div class="brand">
    <span class="brand-dot"></span>
    <span class="brand-name">TELLMORA</span>
  </div>

  <ul class="contact-list">
    <li class="contact-item">48 Harbour Lane, Brisbane
      <span class="contact-icon"><svg viewBox="0 0 10 10"><path d="M1 5 L5 1.5 L9 5 M2.5 4 V8.5 H7.5 V4" fill="none" stroke="#6f6f6f" stroke-width="1"/></svg></span></li>
    <li class="contact-item">(07) 5550 4821
      <span class="contact-icon"><svg viewBox="0 0 10 10"><path d="M3 1 H5 V3 H4 V7 H5 V9 H3 Z" fill="#6f6f6f"/></svg></span></li>
    <li class="contact-item">contact@tellmorafinance.com
      <span class="contact-icon"><svg viewBox="0 0 10 10"><rect x="1" y="2.5" width="8" height="5.5" fill="none" stroke="#6f6f6f"/><path d="M1 2.5 L5 6 L9 2.5" fill="none" stroke="#6f6f6f"/></svg></span></li>
    <li class="contact-item">www.tellmorafinance.com
      <span class="contact-icon"><svg viewBox="0 0 10 10"><circle cx="5" cy="5" r="3.8" fill="none" stroke="#6f6f6f"/><path d="M1.2 5 H8.8 M5 1.2 V8.8" stroke="#6f6f6f" stroke-width="0.7"/></svg></span></li>
  </ul>

  <article class="letter-body">
    <h1 class="headline">Headline</h1>
    <p>HeadingHarume non et, temporror a nis et vernatur sam, aut est et int ut qui ad quodit quibus, ut is quias nos maximin nones comnissi tem quia assinvelissi blab ipicien ihilita volupta volectent delestet fuga. El molupis id quatibusant.</p>
    <p>Pa sundebit esti rem int ped ea sitiandae nitiossi ditatemperi quam sum quid et vel magnati scidunt, volorit aspeditiore, sima cusdae mod molupta nus elitiur soluptatiat.</p>
    <p class="gap">Est, cus ipsanti sitius, illitat ionsequo maionse quistruptat.Bonferum vivide conterum nostum inam immodit, quo ad inatenatum ernius; Catis ius, esta, C. Maequitam, que egit; enata L. Serem hostere ndemqui ia eto conlocae omnesse iam publia modie publiam diors vis Casdamdium actum Palesimus in vis, que in tremorenius, nocte factanuloc, et? quod cer us ignos et auro inte nostem, que actatum tu sent? qua demur prae te coeriaes! Satum ortia? Bon notanda ciena, tatiusquam ista ocut ve, Ti. Fescre, quius, cessest inte taturenterei patiam hos adduci se fuem rem ditalartea di, Ti. Ihilibest ret L. Italicus iam in vehebatem et revirma, vir am hortem patre fica inum sedienit.</p>
    <p class="gap">Pio, quon se ocum portamquid resta et parid ducta sperum confiri sentidea ocae inatieris ta non vivem intem que peri condees sendientidet vis vividemum sescrion hactod conermilis, consil horumenatus ficae vatquam prisquam ipicere derit.</p>
    <p>Obus Catussus cupimum essateridin derionsus hace caver aucon Itam. Niu silis. Caestiam porum sulibusque optilne consulum est? Oposuam demoveheben vides! Sermil hi, praves lius, aut ad publin novicatilis oc tes ordicul inprores det ves! Sendicien adhucon derudam hos auconsu labere ompotis hosta tebat.</p>
    <p>Git. Etra? Nos co tant erudac verfena, C. Cat virtus, quod ignos la res culii senatorte fit es videpsed alincla iam densili caellego esid aticonsilla vid condiendam am ne temquem.</p>
    <p class="gap">Eque ta opora videt, enam o efesser cerivirit; C. me publis, cuppl. Tus Catoribus prachum terterum det? Opica re, manum Patum comnoximorum audeorei ignonlo ctorum octoris convo, quamdiis bondiem dica; inproraríu mandum es et dit vere dea omnit ius fuium paturni hintem, quam publicae re ne in tum is consimis. As ad mediesita efaci praripi entribunum in te diem nernuli cupimmors iam niuropo nsimus mandum ius? Movertem noreoremnit nonveri concendam audeffre pare iam rent vivivis signate runte, norum ac tam.</p>
    <p>Ego ernimus bontilis vis cula Sciviverem spiorum esiliqui is, notanum ina, quam. Decum conde hora ium perfens ultore, quam tem non tem Patum patum avesses imustandit? Nihintiur ute co terum te tatum ta conihil ibulvic audepere patuspica; nos vit pervivive, uro at, querior ute con verrari cientimil hi, cave,</p>
  </article>

  <footer class="sign-off">
    <p class="signature"><span class="signature-mark">SIGNATURE</span>Clara Finch</p>
    <p class="role">Financial Advisor</p>
  </footer>
</main>
</body>
</html>
```